INSTAGRAM STORY FEED FOR LUXURY JEWELRY STORE

For a luxury jewelry retailer. We want to create a set of posts for feed for the post-covid world once we reopen. Our goal is to emphasize the rebirth, the beggining of a new day, with focuses on the REAL important things in life: LOVE (through an engagement rings). LIFE (through baby birth gifts). HAPINESS (through benchmark moments like anniversaries).
Colors must be elegant but happy.
for refference our company Instagram is @quorvane_official so you can have a feel of our brand and product.

Target Market(s)

ENGAGEMENT RINGS. DIAMOND CUSTOMERS. LUXURY RETAIL. LATIN AMERICA.

Industry/Entity Type

Jewelry

Other font styles liked:
• Our logo uses AUDREY

Requirements
Must have
• THEME MUST BE BASED ON A NEW DAY. ELEGANT COLOR SCHEME, WITH LIGHT COLORS, MUST INCLUDE SEVERAL POSTS FOR INSTAGRAM FEED INCLUDING:
Our goal is to emphasize the rebirth, the beggining of a new day, with focuses on the REAL important things in life: LOVE (through an engagement rings). LIFE (through baby birth gifts). HAPINESS (through benchmark moments like anniversaries).
Nice to have
• CLEAN LOOK. PLEASE VIEW IMAGE EXAMPLES OF THINGS I LIKE.
I HAVE POSTED A “LOVE” SIGN IN IMAGES. It would be nice to make something like that sign, in black font, and white, light grey, or even yellow background, and have a ring or piece of jewelrry balancing or hanging from
One of the letters. Then do something similar with word Life, etc.
Should not have
• NO BLACK. NO DARK COLORS. NOTHING THAT WILL LOOK TACKY.

```html
<!DOCTYPE html>
<html lang="en">
<head>
<meta charset="utf-8">
<title>A New Day — Love</title>
<link rel="stylesheet" href="https://fonts.googleapis.com/css2?family=Bodoni+Moda:wght@500&family=Josefin+Sans:wght@300;400&display=swap">
<style>
  :root {
    --peach: #f6c3b1;
    --peach-light: #fbd8c6;
    --peach-deep: #efb3a2;
    --glow: #fff1dc;
    --white: #ffffff;
    --gold: #e6d27a;
    --silver: #e4e4ea;
    --rose: #f1c1b3;
  }
  html, body {
    margin: 0;
    padding: 0;
    overflow: hidden;
  }
  .story {
    position: relative;
    width: 675px;
    height: 1200px;
    overflow: hidden;
    background:
      radial-gradient(circle at 20% 25%, rgba(255,241,220,.55) 0 18px, transparent 40px),
      radial-gradient(circle at 78% 28%, rgba(255,241,220,.5) 0 16px, transparent 38px),
      radial-gradient(circle at 15% 45%, rgba(255,241,220,.45) 0 20px, transparent 44px),
      radial-gradient(circle at 88% 62%, rgba(255,241,220,.35) 0 18px, transparent 42px),
      radial-gradient(circle at 65% 94%, rgba(255,241,220,.45) 0 20px, transparent 46px),
      radial-gradient(ellipse at 70% 40%, var(--peach-light), transparent 60%),
      linear-gradient(170deg, var(--peach) 0%, var(--peach-deep) 55%, var(--peach-light) 100%);
  }
  .backdrop {
    position: absolute;
    inset: 0;
  }
  .frame {
    position: absolute;
    left: 44px;
    top: 53px;
    width: 587px;
    height: 1094px;
    border: 1px solid rgba(255,255,255,.85);
    box-sizing: border-box;
  }
  .tagline {
    position: absolute;
    left: 0;
    right: 0;
    top: 84px;
    margin: 0;
    padding-right: 32px;
    text-align: center;
    font-family: "Josefin Sans", sans-serif;
    font-weight: 300;
    font-size: 25px;
    letter-spacing: 4px;
    color: var(--white);
  }
  .ring {
    position: absolute;
    border-radius: 50% 50% 45% 45%;
  }
  .ring--gold {
    left: 166px; top: 188px; width: 337px; height: 175px;
    background: radial-gradient(ellipse at 50% 35%, var(--white) 0 22%, var(--gold) 55%, transparent 72%);
  }
  .ring--white {
    left: 159px; top: 384px; width: 354px; height: 207px;
    background: radial-gradient(ellipse at 50% 40%, var(--white) 0 28%, var(--silver) 55%, transparent 72%);
  }
  .ring--rose {
    left: 159px; top: 603px; width: 360px; height: 203px;
    background: radial-gradient(ellipse at 50% 40%, var(--white) 0 28%, var(--rose) 55%, transparent 72%);
  }
  .headline {
    position: absolute;
    left: 120px;
    top: 907px;
    margin: 0;
    font-family: "Bodoni Moda", serif;
    font-weight: 500;
    font-size: 173px;
    line-height: 1;
    letter-spacing: -4px;
    white-space: nowrap;
    color: var(--white);
  }
  .brand {
    position: absolute;
    left: 0;
    right: 0;
    top: 1094px;
    text-align: center;
    font-family: "Josefin Sans", sans-serif;
    font-weight: 400;
    font-size: 13px;
    letter-spacing: 3px;
    color: var(--white);
  }
</style>
</head>
<body>
  <main class="story">
    <div class="backdrop" role="img" aria-label="Soft peach background with blurred warm bokeh lights"></div>
    <div class="frame"></div>
    <p class="tagline"># A NEW DAY</p>
    <div class="ring ring--gold" role="img" aria-label="Yellow gold solitaire engagement ring with round diamond and pavé band"></div>
    <div class="ring ring--white" role="img" aria-label="White gold halo engagement ring with split diamond shank"></div>
    <div class="ring ring--rose" role="img" aria-label="Rose gold halo engagement ring with round diamond and pavé band"></div>
    <h1 class="headline">LOVE</h1>
    <div class="brand">QUORVANE</div>
  </main>
</body>
</html>
```